Small Business Consulting Firm Needs Letterhead

We need a letterhead for our company "Brightpath Plus". Our company does outbound calling and mailing to business owner's companies who have taken high interest loans. These loans tend to put these businesses in a big financial bind short term, and we help them find better financial options. We would like the design to match our colors of our logo. Headers and footers would look nice, but we are open. We would want it to include our address, website, phone, and email info. Our address - 2000 E. Lamar Blvd. Suite 600Website - www.safeguardtoday.comEmail - info@safeguardtoday.comPhone - 855-726-1938
Industry/Entity Type
Financial Planning
Look and feel
Each slider illustrates characteristics of the customer's brand and the style your logo design should communicate.

```html
<!DOCTYPE html>
<html lang="en">
<head>
<meta charset="utf-8">
<title>Brightpath Plus Letterhead</title>
<link rel="stylesheet" href="https://fonts.googleapis.com/css2?family=Montserrat:wght@400;500&display=swap">
<style>
  :root {
    --backdrop: #e6e6e4;
    --paper: #ffffff;
    --ink: #2b2b2b;
    --ink-soft: #3d3d3f;
    --brand-green: #6db33f;
    --brand-blue: #1a7cc1;
    --corner-tint: #f1f5f9;
  }
  * { box-sizing: border-box; margin: 0; padding: 0; }
  html, body {
    width: 1200px; height: 1200px; overflow: hidden;
    background: var(--backdrop);
    font-family: "Montserrat", sans-serif;
    color: var(--ink);
  }
  .letterhead {
    position: absolute; left: 170px; top: 45px;
    width: 860px; height: 1110px;
    background: var(--paper);
    box-shadow: 0 6px 18px rgba(0,0,0,0.18);
    overflow: hidden;
  }
  .corner-tint {
    position: absolute; left: 617px; top: 69px;
    width: 174px; height: 174px;
    background: var(--corner-tint);
  }
  .brand {
    position: absolute; top: 54px; left: 0; width: 100%;
    text-align: center;
  }
  .brand-square {
    display: block; width: 64px; height: 64px; margin: 0 auto 30px;
    background: var(--brand-green);
  }
  .brand-name {
    font-size: 25px; font-weight: 400; letter-spacing: 0.04em;
    text-transform: uppercase; color: var(--ink-soft);
  }
  .text-block {
    position: absolute; left: 76px; width: 708px;
    font-size: 14px; letter-spacing: 0.06em; line-height: 22.5px;
  }
  .date { top: 252px; }
  .recipient { top: 311px; }
  .salutation { top: 443px; }
  .body-copy { top: 478px; }
  .body-copy p { text-align: justify; line-height: 25.4px; margin-bottom: 8px; }
  .closing { top: 777px; }
  .signatory { top: 855px; }
  .signatory-name { font-size: 16px; font-weight: 500; letter-spacing: 0.05em; }
  .signatory-role { letter-spacing: 0.35em; margin-top: 2px; }
  .contact-footer {
    position: absolute; top: 1018px; left: 0; width: 100%;
    text-align: center; font-size: 14px; letter-spacing: 0.12em; line-height: 19.5px;
  }
  .footer-rule {
    width: 88px; height: 1px; background: var(--ink); margin: 6px auto 0;
  }
</style>
</head>
<body>
  <main class="letterhead">
    <div class="corner-tint"></div>

    <header class="brand">
      <span class="brand-square"></span>
      <div class="brand-name">Brightpath Plus</div>
    </header>

    <div class="text-block date">Date: 20 November 2018</div>

    <address class="text-block recipient" style="font-style:normal">
      To<br>
      Fernbrook Nursery Ltd.<br>
      48 Alder Crescent, Suite# B<br>
      London, UK 1400B52
    </address>

    <div class="text-block salutation">Dear Harlow,</div>

    <section class="text-block body-copy">
      <p>Lorem Ipsum is simply dummy text of the printing and typesetting industry. Lorem Ipsum has been the industry's standard dummy text ever since the 1500s, when an unknown printer took a galley of type and scrambled it to make a type specimen book. It has survived not only five centuries, but also the leap into electronic typesetting, remaining essentially unchanged. It was popularised in the 1960s with the release of Letterline sheets containing Lorem Ipsum passages, and more recently with desktop publishing software like Folio PageComposer including versions of Lorem Ipsum.</p>
      <p>Lorem Ipsum is simply dummy text of the printing and typesetting industry. Lorem Ipsum has been the industry's.</p>
    </section>

    <div class="text-block closing">Thanking you</div>

    <div class="text-block signatory">
      <div class="signatory-name">Daniel Reeve</div>
      <div class="signatory-role">CEO</div>
    </div>

    <footer class="contact-footer">
      <div>4170 W. Corwin Ave. Suite 310</div>
      <div>P: 855-726-1938 | E: info@brightpathplus.com</div>
      <div>www.brightpathplus.com</div>
      <div class="footer-rule"></div>
    </footer>
  </main>
</body>
</html>
```